Brookvale Building Company - advertisement poster

I am looking to print some canvas signs to advertise my general contracting company, Brookvale Building Company. The sign will measure 6' long x 3' high so the size should match that ratio. I already have a logo icon, which is the Letter 'B' and some trees that I would like to incorporate, see attached. I would also like the to have the following information listed:
1) phone number: 831-555-0172
2) email: brookvalebuildingcompany@mailnest.example
3) website: brookvalebuildingcompany.example
4) Lic#4826130
5) I want to use this text: "BUILD WITH THE B-CREW!"

The ad should be relatively simple and clean. Black and Green are my company colors. I am open to creative ideas!

Target Market(s)

People looking to renovate their homes

Industry/Entity Type

Construction

Colors
59FF00
82FF00
B8FF75
E3FFCB
F4FFEA

Requirements
Must have
• Must have my company logo
Should not have
• No photos or complex graphics

```html
<!DOCTYPE html>
<html lang="en">
<head>
<meta charset="utf-8">
<title>Brookvale Building Company – Sign</title>
<link href="https://fonts.googleapis.com/css2?family=Russo+One&family=Oxanium:wght@500;700&display=swap" rel="stylesheet">
<style>
  :root {
    --ink: #1f1f1e;
    --paper: #f4f3ef;
    --green: #86c854;
    --white: #ffffff;
    --backdrop: #e6e6e3;
  }
  html, body {
    margin: 0;
    width: 1200px;
    height: 900px;
    overflow: hidden;
    background: var(--backdrop);
  }
  .sign {
    position: absolute;
    left: 40px;
    top: 170px;
    width: 1120px;
    height: 560px;
    background: var(--paper);
    overflow: hidden;
  }
  .sign__panel {
    position: absolute;
    inset: 0;
  }
  .brand {
    position: absolute;
    left: 40px;
    top: 70px;
    width: 320px;
    text-align: center;
  }
  .brand__mark {
    display: block;
    width: 26px;
    height: 26px;
    background: var(--green);
    margin: 0 auto 16px;
  }
  .brand__name {
    font-family: "Oxanium", sans-serif;
    font-weight: 700;
    color: var(--white);
    margin: 0;
    line-height: 1.1;
    letter-spacing: 1px;
  }
  .brand__name-main { display: block; font-size: 46px; }
  .brand__name-sub { display: block; font-size: 18px; letter-spacing: 5px; margin-top: 4px; }
  .brand__license {
    font-family: "Oxanium", sans-serif;
    font-weight: 700;
    font-size: 18px;
    color: var(--green);
    margin: 8px 0 0;
    letter-spacing: 1px;
  }
  .contact {
    position: absolute;
    left: 32px;
    bottom: 50px;
    margin: 0;
    padding: 0;
    list-style: none;
    font-family: "Oxanium", sans-serif;
    color: var(--white);
  }
  .contact__item {
    display: flex;
    align-items: center;
    gap: 8px;
    margin-top: 12px;
    font-size: 16px;
    font-weight: 500;
    letter-spacing: 0.5px;
  }
  .contact__item--phone {
    font-size: 30px;
    font-weight: 700;
    letter-spacing: 2px;
  }
  .contact__icon { width: 18px; height: 18px; flex: none; }
  .headline {
    margin: 0;
    font-family: "Russo One", sans-serif;
    font-weight: 400;
    color: var(--ink);
  }
  .headline__lead,
  .headline__mark,
  .headline__tail {
    position: absolute;
    right: 36px;
    white-space: nowrap;
    line-height: 1;
  }
  .headline__lead {
    top: 56px;
    font-size: 58px;
    letter-spacing: 1px;
  }
  .headline__mark {
    top: 215px;
    right: 70px;
    display: flex;
    align-items: center;
    gap: 18px;
    font-size: 50px;
    color: var(--green);
    letter-spacing: 2px;
  }
  .headline__mark-square {
    width: 44px;
    height: 44px;
    background: var(--green);
  }
  .headline__tail {
    bottom: 42px;
    font-size: 90px;
  }
</style>
</head>
<body>
  <section class="sign" aria-label="Brookvale Building Company sign">
    <svg class="sign__panel" width="1120" height="560" viewBox="0 0 1120 560" aria-hidden="true">
      <polygon points="0,0 340,0 650,560 0,560" fill="var(--ink)"/>
    </svg>

    <div class="brand">
      <span class="brand__mark"></span>
      <p class="brand__name">
        <span class="brand__name-main">BROOKVALE</span>
        <span class="brand__name-sub">BUILDING COMPANY</span>
      </p>
      <p class="brand__license">Lic#4826130</p>
    </div>

    <ul class="contact">
      <li class="contact__item contact__item--phone">
        <svg class="contact__icon" viewBox="0 0 24 24" fill="none" stroke="var(--green)" stroke-width="2.4"><circle cx="12" cy="12" r="10"/><path d="M8.5 7.5l2 2-1 1.5c.8 1.6 1.9 2.7 3.5 3.5l1.5-1 2 2-1.2 1.5c-3.8-.4-7.4-4-7.8-7.8z"/></svg>
        831-555-0172
      </li>
      <li class="contact__item">
        <svg class="contact__icon" viewBox="0 0 24 24" fill="none" stroke="var(--green)" stroke-width="2.4"><rect x="2" y="5" width="20" height="14" rx="2"/><path d="M3 6l9 7 9-7"/></svg>
        brookvalebuildingcompany@mailnest.example
      </li>
      <li class="contact__item">
        <svg class="contact__icon" viewBox="0 0 24 24" fill="none" stroke="var(--green)" stroke-width="2.2"><circle cx="12" cy="12" r="10"/><ellipse cx="12" cy="12" rx="4.5" ry="10"/><path d="M2 12h20M4 7h16M4 17h16"/></svg>
        brookvalebuildingcompany.example
      </li>
    </ul>

    <h1 class="headline">
      <span class="headline__lead">BUILD WITH THE</span>
      <span class="headline__mark"><span class="headline__mark-square"></span>BROOKVALE</span>
      <span class="headline__tail">B-CREW!</span>
    </h1>
  </section>
</body>
</html>
```